Business card for acupunctist in Melbourne. Specialises in Fertility, pre and post natal care, pain

I am looking for a business card which is going to catch people eyes. Two sided, one side in a muted colour (keeping it feminine) (pink or yellow???)maybe with a little simple logo or picture, the other side I was thinking white with 3 colours (pink grey and yellow... Had these in mind.
Info on the card
Mirren Costa Acupuncture

Dr Mirren Costa (TCM Acupuncture)
Acupuncture for balancing body and mind.
Willowmere Therapeutics
14 Ferndale Road, Oakhurst 3071.
94726151
0428319574
Mirrentcm@quillpost.net

Some other little logo/ designs I have liked are as follows:
http://www.dorotheabrisklac.net/rates-and-insurance/
http://www.rosalindpeverell.net/
http://www.tz-acupuncture.example.uk/

Target Market(s)

professional women, people in pain, active people, people seeking a healthy lifefstyle.

Industry/Entity Type

Business

Font styles to use
Serif
Sans Serif

Colors
eea4c8
fde08a
aaaaaa

Requirements
Must have
• Must be eye catching, but not too loud and busy. Subltle is good. Simple is also good. The logo could be something that represents growth and health and nurturing. Again not too elaborate, very simple.
Thankyou
Should not have
• Electric colours, crazy fonts, Pictures of yin and yang, candles, or bodies.

```html
<!DOCTYPE html>
<html lang="en">
<head>
<meta charset="utf-8">
<title>Mirren Costa Acupuncture – Business Card</title>
<link rel="stylesheet" href="https://fonts.googleapis.com/css2?family=Tinos&family=Open+Sans:wght@400;600;700&display=swap">
<style>
  :root {
    --bg: #e9e9e9;
    --card: #ffffff;
    --pink: #eea4c8;
    --pink-deep: #e58ab8;
    --yellow: #fde08a;
    --grey: #aaaaaa;
    --grey-faint: #ececec;
    --ink: #2b2b2b;
    --ink-soft: #555555;
  }
  * { box-sizing: border-box; margin: 0; padding: 0; }
  html, body { width: 1200px; height: 1200px; overflow: hidden; }
  body {
    background: var(--bg);
    display: flex;
    flex-direction: column;
    align-items: center;
    justify-content: center;
    gap: 60px;
  }
  .card {
    position: relative;
    width: 700px;
    height: 400px;
    background: var(--card);
    box-shadow: 0 10px 30px rgba(0,0,0,0.10);
    overflow: hidden;
  }

  /* Front */
  .front-decoration {
    position: absolute;
    top: 0;
    left: 0;
    width: 520px;
    height: 300px;
    background: radial-gradient(ellipse at 40% 40%, var(--grey-faint) 0%, rgba(236,236,236,0.5) 45%, rgba(255,255,255,0) 75%);
  }
  .front-brand {
    position: absolute;
    left: 230px;
    top: 170px;
    display: flex;
    align-items: center;
    gap: 22px;
  }
  .brand-dot {
    width: 70px;
    height: 70px;
    border-radius: 50%;
    background: var(--pink);
    flex: none;
  }
  .front-name {
    font-family: "Tinos", serif;
    font-weight: 400;
    font-size: 40px;
    line-height: 1.05;
    color: var(--pink-deep);
  }

  /* Back */
  .back-brand {
    position: absolute;
    left: 70px;
    top: 120px;
    width: 130px;
    height: 130px;
    border-radius: 50%;
    background: var(--pink);
  }
  .back-details {
    position: absolute;
    left: 270px;
    top: 105px;
    font-family: "Open Sans", sans-serif;
    color: var(--ink);
  }
  .practitioner {
    font-size: 24px;
    font-weight: 700;
  }
  .practitioner .credential {
    font-size: 14px;
    font-weight: 400;
    color: var(--ink-soft);
  }
  .tagline, .clinic {
    font-size: 14px;
    color: var(--ink-soft);
    line-height: 1.35;
  }
  .contact-list {
    list-style: none;
    margin-top: 26px;
  }
  .contact-list li {
    display: flex;
    align-items: center;
    gap: 10px;
    font-size: 17px;
    line-height: 1.6;
  }
  .contact-icon { width: 16px; height: 16px; flex: none; }
</style>
</head>
<body>

  <section class="card card-front" aria-label="Card front">
    <div class="front-decoration" role="img" aria-label="Faint grey petal shapes and scattered dots"></div>
    <div class="front-brand">
      <span class="brand-dot"></span>
      <p class="front-name">Mirren Costa<br>Acupuncture</p>
    </div>
  </section>

  <section class="card card-back" aria-label="Card back">
    <span class="back-brand"></span>
    <div class="back-details">
      <p class="practitioner">Dr Mirren Costa <span class="credential">(TCM Acupuncture)</span></p>
      <p class="tagline">Acupuncture for balancing body and mind.</p>
      <p class="clinic">Willowmere Therapeutics</p>
      <ul class="contact-list">
        <li>
          <svg class="contact-icon" viewBox="0 0 16 16"><circle cx="8" cy="8" r="8" fill="#eea4c8"/><path d="M8 3.5a2.8 2.8 0 0 0-2.8 2.8C5.2 8.5 8 12.5 8 12.5s2.8-4 2.8-6.2A2.8 2.8 0 0 0 8 3.5z" fill="#fff"/><circle cx="8" cy="6.3" r="1" fill="#eea4c8"/></svg>
          14 Ferndale Road, Oakhurst 3071
        </li>
        <li>
          <svg class="contact-icon" viewBox="0 0 16 16"><circle cx="8" cy="8" r="8" fill="#eea4c8"/><path d="M5.2 4h1.6l.8 2-1 .8a5 5 0 0 0 2.6 2.6l.8-1 2 .8v1.6c0 .5-.4.9-.9.9A7.3 7.3 0 0 1 4.3 4.9c0-.5.4-.9.9-.9z" fill="#fff"/></svg>
          94726151
        </li>
        <li>
          <svg class="contact-icon" viewBox="0 0 16 16"><circle cx="8" cy="8" r="8" fill="#eea4c8"/><rect x="5.5" y="3.5" width="5" height="9" rx="1" fill="#fff"/><circle cx="8" cy="11" r=".6" fill="#eea4c8"/></svg>
          0428319574
        </li>
        <li>
          <svg class="contact-icon" viewBox="0 0 16 16"><circle cx="8" cy="8" r="8" fill="#eea4c8"/><rect x="4" y="5" width="8" height="6" rx=".8" fill="#fff"/><path d="M4.3 5.4 8 8.3l3.7-2.9" fill="none" stroke="#eea4c8" stroke-width=".9"/></svg>
          Mirrentcm@quillpost.net
        </li>
      </ul>
    </div>
  </section>

</body>
</html>
```